Tire trade

Hello, I would like to make A5 flyers for my garage, with the 'marvek tires' logo.
Registration: Sale and fitting of tires of all brands (also ordered by you) Guarding of your tires

Target Market(s)

All motorists in my area

Industry/Entity Type

Vente de pneus

Font styles to use
Serif

Colors
EE7325
F08F49
F5BC92
FAE3D3
FDF4ED

Requirements
Must have
• My logo, the place (Val-d'Orsenne)
Nice to have
• Simple and eye-catching
Should not have
• pink

```html
<!DOCTYPE html>
<html lang="en">
<head>
<meta charset="utf-8">
<title>marvek tires – A5 flyer, front and back</title>
<link rel="stylesheet" href="https://fonts.googleapis.com/css2?family=Montserrat:ital,wght@0,800;0,900;1,800;1,900&display=swap">
<style>
  :root {
    --stage: #1c1c1c;
    --orange: #ee7325;
    --orange-light: #f08f49;
    --amber: #ffb000;
    --red-deep: #7a0a02;
    --red: #d62a0c;
    --red-bright: #ff3a12;
    --white: #ffffff;
    --ink: #000000;
    --shadow: #140200;
  }
  * { box-sizing: border-box; margin: 0; padding: 0; }
  html, body {
    width: 1200px; height: 912px; overflow: hidden;
    background: var(--stage);
    font-family: "Montserrat", Arial, sans-serif;
  }
  .canvas { position: relative; width: 1200px; height: 912px; }

  .flyer {
    position: absolute; top: 131px;
    width: 419px; height: 595px; overflow: hidden;
  }
  .flyer--front { left: 132px; }
  .flyer--back { left: 644px; background: var(--ink); }

  .flyer__photo {
    position: absolute; inset: 0;
    background:
      radial-gradient(ellipse 150px 170px at 210px 295px, rgba(0,0,0,.92), rgba(0,0,0,0) 100%),
      radial-gradient(ellipse 240px 120px at 60px 250px, rgba(255,70,20,.6), rgba(255,70,20,0)),
      linear-gradient(180deg, #c8182a 0%, var(--red) 28%, #a11405 55%, var(--red-deep) 72%, #b01b08 88%, #6e0d04 100%);
  }

  .headline {
    position: absolute; left: 0; right: 0; top: 30px;
    text-align: center; color: var(--white);
    font-weight: 900; font-style: italic;
    font-size: 31px; line-height: 25px; letter-spacing: -1.5px;
    text-transform: uppercase;
    text-shadow: 3px 3px 0 var(--shadow);
  }
  .subline {
    position: absolute; left: 0; right: 0; top: 134px;
    text-align: center; color: var(--shadow);
    font-weight: 900; font-style: italic;
    font-size: 16px; letter-spacing: -.5px;
    text-transform: uppercase;
  }

  .brand {
    position: absolute; left: 0; right: 0;
    display: flex; align-items: center; justify-content: center; gap: 10px;
    color: var(--orange);
    font-weight: 900; font-size: 44px; letter-spacing: -1px;
    text-transform: lowercase;
  }
  .brand__dot {
    width: 16px; height: 16px; border-radius: 50%;
    background: var(--orange);
  }
  .flyer--front .brand { top: 248px; }
  .flyer--back .brand { top: 172px; }

  .phone {
    position: absolute; left: 0; right: 0;
    text-align: center;
    font-weight: 900; font-style: italic;
    font-size: 29px; letter-spacing: -.5px;
    color: var(--orange-light);
  }
  .flyer--front .phone { top: 312px; }
  .flyer--back .phone { top: 236px; }

  .service {
    position: absolute; left: 0; right: 0; top: 462px;
    text-align: center;
    font-weight: 900; font-style: italic;
    font-size: 45px; line-height: 36px; letter-spacing: -2px;
    text-transform: uppercase;
    background: linear-gradient(180deg, var(--amber) 0%, var(--orange) 55%, var(--red-bright) 100%);
    -webkit-background-clip: text; background-clip: text;
    color: transparent;
    filter: drop-shadow(3px 3px 0 var(--shadow));
  }

  .place {
    position: absolute; left: 0; right: 0; top: 417px;
    text-align: center; color: var(--orange);
    font-weight: 900; font-style: italic;
    font-size: 17px; letter-spacing: -.3px;
    text-transform: uppercase;
  }
</style>
</head>
<body>
<main class="canvas">

  <section class="flyer flyer--front">
    <div class="flyer__photo" role="img" aria-label="Photo of alloy wheels and tires and a car wheel arch lit in red and orange light"></div>
    <h1 class="headline">Sale and fitting<br>of tires of all<br>brands</h1>
    <p class="subline">(also ordered by you)</p>
    <div class="brand"><span class="brand__dot"></span>marvek tires</div>
    <p class="phone">079/555.40.18</p>
    <p class="service">Guarding of<br>your tires!</p>
  </section>

  <section class="flyer flyer--back">
    <div class="brand"><span class="brand__dot"></span>marvek tires</div>
    <p class="phone">079/555.40.18</p>
    <p class="place">Val-d'Orsenne</p>
  </section>

</main>
</body>
</html>
```